Velmo Swinger site - new website, blogsite and merchandise point, connection to tradeva

We are a well established Swingers Club in the North east of UK and already have an existing site. www.velmo-example.co.uk, BUT we have changed our logo and our information on the site needs to be updated.

We are changing our hosting site to Nimbrashost.example ,also wanting to start a blog which is linked to the club, plus we wish to sell a small exclusive range of Velmo linked merchandise which will also be available on Tradeva.

I have attached a pdf of the majority of the content. additionally we will provide pictures and a videoclip which should be able to be viewed by pc's, lap tops and mobile phones (the whole website must be fully accessible via phone).

The new site must be able to be updated by someone with medium computer knowledge (usually me), by no means expert. Updates will generally be new pictures and written information. The site must be able to be transferred to NimbrasHost.

Velmo is one of the countries leading clubs and emphasises friendliness, fun & safety for its members, we look after you to ensure your experience is the best we can offer. We are very proud of our reputation, built up over more than 10 years.

Target Market(s)

Swingers, dreamers & fantasists, alternative lifestyle people

Coding

Coded - Design and coding required

Number of Pages Required

5+ page

Font styles to use
Sans Serif

Colors
000000
ec1f27
fbfbfb
eeeeee
eaeaea

Requirements
Must have
• website with blog attached, link to tradeva & quidlo, ability to run videoclip and picture album and must be compatable to transfer easily to Nimbrashost and be updated by non-professional (who can learn)
• Straightforward & easy to navigate
• over 18 content page with enter button
Nice to have
• sexy site
• link to chirpster maybe
• black site would be nice with red or white writing
Should not have
• children and animals in anyway shape or form

```html
<!DOCTYPE html>
<html lang="en">
<head>
<meta charset="utf-8">
<title>Velmo – Members Club</title>
<link rel="stylesheet" href="https://fonts.googleapis.com/css2?family=Cinzel:wght@400;700&family=Open+Sans:wght@400;600;700&display=swap">
<style>
:root{
  --red:#ec1f27;
  --black:#000000;
  --white:#fbfbfb;
  --grey:#eeeeee;
  --grey-2:#eaeaea;
  --panel:#1a1a1a;
  --ink:#111111;
  --muted:#b9b9b9;
  --head:'Cinzel',serif;
  --body:'Open Sans',sans-serif;
}
*{box-sizing:border-box;margin:0;padding:0}
html,body{width:1200px;height:4100px;overflow:hidden}
body{position:relative;background:var(--black);font-family:var(--body);color:var(--white)}
a{color:inherit;text-decoration:none}
.wrap{width:1004px;margin:0 auto;position:relative}
.section-title{font-family:var(--head);font-weight:400;text-align:center;font-size:38px;letter-spacing:1px}

/* header + hero */
.hero{height:533px;position:relative;background:linear-gradient(180deg,#0d1626 0%,#1d2a3e 45%,#39352d 80%,#1a1714 100%)}
.hero-photo{position:absolute;inset:0}
.topbar{position:absolute;top:10px;right:98px;display:flex;gap:28px;font-size:14px;color:var(--grey)}
.topbar span::before{content:"";display:inline-block;width:9px;height:9px;background:var(--red);border-radius:50%;margin-right:8px}
.site-header{position:absolute;top:28px;left:98px;right:98px;display:flex;align-items:center;justify-content:space-between}
.brand{font-family:var(--head);font-size:44px;color:var(--white);letter-spacing:2px}
.main-nav{display:flex;gap:20px;font-size:15px;color:var(--grey)}
.main-nav a.active{color:var(--red)}
.hero-title{position:absolute;top:150px;width:100%;text-align:center;font-family:var(--head);font-size:66px;letter-spacing:6px}
.hero-sub{position:absolute;top:256px;width:100%;text-align:center;font-size:22px;color:var(--grey)}

/* welcome */
.welcome{height:711px;background:var(--red);padding-top:78px}
.welcome .intro{width:880px;margin:22px auto 0;text-align:center;font-size:14px;line-height:22px;color:var(--white)}
.features{display:grid;grid-template-columns:repeat(4,1fr);row-gap:48px;margin-top:52px}
.feature{text-align:center}
.feature svg{width:60px;height:60px;fill:none;stroke:var(--white);stroke-width:4}
.feature h3{font-family:var(--head);font-weight:400;font-size:22px;margin:14px 0 8px}
.feature p{font-size:13px;line-height:19px;width:200px;margin:0 auto}

/* about */
.about{height:505px;background:#2a1616;padding-top:62px}
.about .wrap{display:flex;gap:55px}
.about-photo{width:405px;height:383px;border:3px solid #444;background:linear-gradient(150deg,#3a0b0c,#8a1b1d 50%,#2a0808)}
.about-text h2{font-family:var(--head);font-weight:400;font-size:38px;line-height:46px}
.about-text p{font-size:14px;line-height:22px;margin-top:18px;color:var(--grey)}
.btn-outline{display:inline-block;margin-top:28px;border:2px solid var(--red);color:var(--red);padding:10px 22px;font-size:13px;font-weight:600;text-transform:uppercase}

/* membership */
.membership{height:396px;background:#141414;padding-top:90px}
.membership .wrap{display:flex;justify-content:space-between}
.member-card{width:481px;height:216px;border:3px solid #555;display:flex;gap:22px;padding:14px;background:#000}
.member-photo{width:200px;height:182px;background:linear-gradient(160deg,#5b2222,#a3342c 60%,#2b1010)}
.member-body h3{font-family:var(--head);font-weight:400;color:var(--red);font-size:20px;margin-top:6px}
.member-body p{font-size:13px;line-height:19px;margin-top:10px}
.btn-red{display:inline-block;margin-top:18px;background:var(--red);color:var(--white);padding:12px 26px;font-size:13px;font-weight:600;text-transform:uppercase}

/* blog */
.blog{height:397px;background:#2a1414;padding-top:52px}
.posts{display:flex;justify-content:space-between;margin-top:46px}
.post{width:470px;display:flex;gap:22px}
.post-photo{width:180px;height:142px;border:3px solid #555;background:linear-gradient(160deg,#3b2412,#8f5a24 55%,#1c0f07)}
.post h3{font-family:var(--head);font-weight:400;font-size:17px;line-height:22px}
.post .meta{font-size:12px;color:var(--muted);margin-top:8px}
.post p{font-size:13px;line-height:19px;margin-top:8px}
.post .more{display:block;color:var(--red);font-size:13px;margin-top:8px}

/* products */
.products{height:1284px;background:#2b2b2b;padding-top:68px}
.product-grid{display:grid;grid-template-columns:repeat(4,238px);column-gap:19px;row-gap:121px;margin-top:40px}
.product-thumb{height:216px;background:#c8c8c8;display:flex;align-items:center;justify-content:center;font-family:var(--body);font-weight:700;font-size:22px;color:#7a7a7a}
.product p{font-size:14px;line-height:20px;margin-top:16px}
.product-foot{display:flex;justify-content:space-between;align-items:center;margin-top:4px}
.price{color:var(--red);font-size:14px}
.store{font-weight:700;font-size:15px;color:var(--white)}

/* footer */
.site-footer{height:274px;background:var(--black);border-top:3px solid var(--red);padding-top:56px}
.contacts{display:flex;justify-content:center;gap:60px;font-size:13px}
.contact{display:flex;align-items:center;gap:14px}
.contact .ring{width:44px;height:44px;border:2px solid #555;border-radius:50%;display:flex;align-items:center;justify-content:center}
.contact svg{width:18px;height:18px;fill:var(--white)}
.footer-nav{display:flex;justify-content:center;gap:22px;margin-top:26px;font-size:13px;font-weight:600}
.footer-base{display:flex;justify-content:space-between;align-items:center;margin-top:40px;font-size:12px;color:var(--muted)}
.socials{display:flex;gap:10px}
.socials span{width:32px;height:32px;border:2px solid #666;border-radius:50%}

/* age gate */
.veil{position:absolute;inset:0;background:rgba(0,0,0,.58)}
.age-gate{position:absolute;top:191px;left:251px;width:700px;height:397px;border:3px solid var(--white);background:linear-gradient(120deg,#3a2618 0%,#14100d 35%,#0d0a08 100%);text-align:center;padding-top:68px}
.age-gate h1{font-family:var(--head);font-weight:700;font-size:30px;letter-spacing:.5px}
.age-gate p{width:500px;margin:18px auto 0;font-size:14px;line-height:22px}
.gate-actions{display:flex;justify-content:center;gap:66px;margin-top:44px}
.gate-choice{width:140px}
.gate-btn{display:block;height:70px;line-height:70px;font-size:22px;font-weight:600;text-transform:uppercase}
.gate-btn.enter{background:var(--red);color:var(--white)}
.gate-btn.exit{background:var(--white);color:var(--ink)}
.gate-choice small{display:block;margin-top:14px;font-size:12px}
</style>
</head>
<body>

<header class="hero">
  <div class="hero-photo" role="img" aria-label="Night skyline of the city with lit buildings"></div>
  <div class="topbar"><span>0700 555 0142</span><span>velmoswingers@mailbox.example</span></div>
  <div class="site-header">
    <a class="brand" href="#">VELMO</a>
    <nav class="main-nav">
      <a class="active" href="#">Home</a><a href="#">Diary</a><a href="#">Theme Parties</a><a href="#">TVTG and Admirers</a><a href="#">Membership</a><a href="#">FAQs</a><a href="#">Rooms</a><a href="#">Contact Us</a><a href="#">Links</a>
    </nav>
  </div>
  <div class="hero-title">VELMO</div>
  <div class="hero-sub">Welcome to one of the leading members clubs</div>
</header>

<section class="welcome">
  <h2 class="section-title">Welcome to Velmo</h2>
  <p class="intro">We are the best in the North East and were recently voted No 2 club in the UK. We have received the coveted title of No 1 Friendliest Club in the UK 2nd year in place with our great friends "Night Owl Guide".</p>
  <div class="wrap features">
    <div class="feature"><svg viewBox="0 0 60 60"><circle cx="14" cy="30" r="7"/><circle cx="44" cy="14" r="7"/><circle cx="44" cy="46" r="7"/><path d="M20 27l18-10M20 33l18 10"/></svg><h3>Social Area</h3><p>Relax with friends and drinks in a warm, easy lounge.</p></div>
    <div class="feature"><svg viewBox="0 0 60 60"><rect x="6" y="18" width="48" height="26" rx="12"/><path d="M18 26v10M13 31h10"/><circle cx="40" cy="28" r="2"/><circle cx="45" cy="34" r="2"/></svg><h3>Play Rooms</h3><p>Private and open rooms set out for every kind of mood.</p></div>
    <div class="feature"><svg viewBox="0 0 60 60"><path d="M12 50V28a18 18 0 0 1 36 0v22H38V28a8 8 0 0 0-16 0v22z"/></svg><h3>BDSM Dungeon</h3><p>A fully fitted dungeon with kit for the bold at heart.</p></div>
    <div class="feature"><svg viewBox="0 0 60 60"><path d="M8 22h44l-4-12H12zM12 22v30h36V22M24 52V36h12v16"/></svg><h3>Exhibition Area</h3><p>A lit stage for those who love to be watched.</p></div>
    <div class="feature"><svg viewBox="0 0 60 60"><rect x="16" y="10" width="28" height="42"/><path d="M22 18h4M34 18h4M22 28h4M34 28h4M22 38h4M34 38h4"/></svg><h3>Amsterdam Room</h3><p>Window rooms styled on the famous red light streets.</p></div>
    <div class="feature"><svg viewBox="0 0 60 60"><path d="M30 8C22 22 16 30 16 38a14 14 0 0 0 28 0c0-8-6-16-14-30z"/></svg><h3>Wet Areas</h3><p>Showers, sauna and steam room kept clean and warm.</p></div>
    <div class="feature"><svg viewBox="0 0 60 60"><rect x="14" y="8" width="32" height="44"/><path d="M20 16h6M34 16h6M20 26h6M34 26h6M26 52V40h8v12"/></svg><h3>Hotel Rooms</h3><p>Stay over in comfort after a long night of fun.</p></div>
    <div class="feature"><svg viewBox="0 0 60 60"><circle cx="22" cy="40" r="12"/><path d="M30 32L50 12M44 10l6 6"/></svg><h3>Crash Space</h3><p>Quiet chill out zones when you need a calm break.</p></div>
  </div>
</section>

<section class="about">
  <div class="wrap">
    <div class="about-photo" role="img" aria-label="Red lit club play room with a cross frame"></div>
    <div class="about-text">
      <h2>Velmo :: A Great<br>Place To Meet And Play!</h2>
      <p>We are the best Swingers Club in the North East, and also voted No 2 club in the UK.</p>
      <p>We have received the coveted title of No 1 friendliest club in the UK 2nd year in place with our great friends "Night Owl Guide". The prestigious award has been given to us by a panel of 8 anonymous swingers, singles and couples working with the publication called "Out on the Town", a copy of which is available in reception. Please see our Frequently Asked Questions and Membership pages for more information about the club and its facilities. Velmo was established in Sunderland in 2004 by Alex.</p>
      <a class="btn-outline" href="#">Read More</a>
    </div>
  </div>
</section>

<section class="membership">
  <div class="wrap">
    <article class="member-card">
      <div class="member-photo" role="img" aria-label="Club bedroom with red walls"></div>
      <div class="member-body"><h3>Membership Fees</h3><p>New members (Couples and Single guys) - annual £35, this now includes the new 2 visit half price.</p><a class="btn-red" href="#">Read More</a></div>
    </article>
    <article class="member-card">
      <div class="member-photo" role="img" aria-label="Club lounge room with framed wall art"></div>
      <div class="member-body"><h3>Membership Discounts</h3><p>We discount entry and membership to support the Members Forum running and rebuild.</p><a class="btn-red" href="#">Read More</a></div>
    </article>
  </div>
</section>

<section class="blog">
  <h2 class="section-title">Our Blog</h2>
  <div class="wrap posts">
    <article class="post">
      <div class="post-photo" role="img" aria-label="Club bar room with warm lighting"></div>
      <div><h3>At Vero Eos Et Accusamus Et Iusto Odio Dignissima</h3><div class="meta">11/06/2017 &nbsp; Alex</div><p>Lorem ipsum dolor sit amet, consectetur adipiscing elit sed do eiusmod.</p><a class="more" href="#">Read More →</a></div>
    </article>
    <article class="post">
      <div class="post-photo" role="img" aria-label="Club room with dark furniture and a doorway"></div>
      <div><h3>At Vero Eos Et Accusamus Et Iusto Odio Dignissima</h3><div class="meta">11/06/2017 &nbsp; Alex</div><p>Lorem ipsum dolor sit amet, consectetur adipiscing elit sed do eiusmod.</p><a class="more" href="#">Read More →</a></div>
    </article>
  </div>
</section>

<section class="products">
  <h2 class="section-title">Velmo Products</h2>
  <div class="wrap product-grid">
    <div class="product"><div class="product-thumb">COMING SOON</div><p>At vero eos et accusamus iusto odio dignissimos duc.</p><div class="product-foot"><span class="price">$20.00</span><span class="store">tradeva</span></div></div>
    <div class="product"><div class="product-thumb">COMING SOON</div><p>At vero eos et accusamus iusto odio dignissimos duc.</p><div class="product-foot"><span class="price">$20.00</span><span class="store">tradeva</span></div></div>
    <div class="product"><div class="product-thumb">COMING SOON</div><p>At vero eos et accusamus iusto odio dignissimos duc.</p><div class="product-foot"><span class="price">$20.00</span><span class="store">tradeva</span></div></div>
    <div class="product"><div class="product-thumb">COMING SOON</div><p>At vero eos et accusamus iusto odio dignissimos duc.</p><div class="product-foot"><span class="price">$20.00</span><span class="store">tradeva</span></div></div>
    <div class="product"><div class="product-thumb">COMING SOON</div><p>At vero eos et accusamus iusto odio dignissimos duc.</p><div class="product-foot"><span class="price">$20.00</span><span class="store">tradeva</span></div></div>
    <div class="product"><div class="product-thumb">COMING SOON</div><p>At vero eos et accusamus iusto odio dignissimos duc.</p><div class="product-foot"><span class="price">$20.00</span><span class="store">tradeva</span></div></div>
    <div class="product"><div class="product-thumb">COMING SOON</div><p>At vero eos et accusamus iusto odio dignissimos duc.</p><div class="product-foot"><span class="price">$20.00</span><span class="store">tradeva</span></div></div>
    <div class="product"><div class="product-thumb">COMING SOON</div><p>At vero eos et accusamus iusto odio dignissimos duc.</p><div class="product-foot"><span class="price">$20.00</span><span class="store">tradeva</span></div></div>
    <div class="product"><div class="product-thumb">COMING SOON</div><p>At vero eos et accusamus iusto odio dignissimos duc.</p><div class="product-foot"><span class="price">$20.00</span><span class="store">tradeva</span></div></div>
    <div class="product"><div class="product-thumb">COMING SOON</div><p>At vero eos et accusamus iusto odio dignissimos duc.</p><div class="product-foot"><span class="price">$20.00</span><span class="store">tradeva</span></div></div>
    <div class="product"><div class="product-thumb">COMING SOON</div><p>At vero eos et accusamus iusto odio dignissimos duc.</p><div class="product-foot"><span class="price">$20.00</span><span class="store">tradeva</span></div></div>
    <div class="product"><div class="product-thumb">COMING SOON</div><p>At vero eos et accusamus iusto odio dignissimos duc.</p><div class="product-foot"><span class="price">$20.00</span><span class="store">tradeva</span></div></div>
  </div>
</section>

<footer class="site-footer">
  <div class="contacts">
    <div class="contact"><span class="ring"><svg viewBox="0 0 20 20"><path d="M10 1a6 6 0 0 0-6 6c0 5 6 12 6 12s6-7 6-12a6 6 0 0 0-6-6zm0 8a2 2 0 1 1 0-4 2 2 0 0 1 0 4z"/></svg></span><span>12 Harbour Lane, 3rd Floor<br>Sunderland</span></div>
    <div class="contact"><span class="ring"><svg viewBox="0 0 20 20"><path d="M4 2l4 1 1 4-2 2c1 2 3 4 5 5l2-2 4 1 1 4-2 1C9 18 2 11 2 4z"/></svg></span><span>0700 555 0142</span></div>
    <div class="contact"><span class="ring"><svg viewBox="0 0 20 20"><path d="M2 5h16v10H2zM2 5l8 6 8-6" fill="none" stroke="#fbfbfb" stroke-width="1.6"/></svg></span><span>velmoswingers@mailbox.example</span></div>
  </div>
  <nav class="footer-nav"><a href="#">HOME</a><a href="#">DIARY</a><a href="#">THEME PARTIES</a><a href="#">TVTG AND ADMIRERS</a><a href="#">MEMBERSHIP</a><a href="#">FAQS</a><a href="#">ROOMS</a><a href="#">CONTACT US</a><a href="#">LINKS</a></nav>
  <div class="wrap footer-base"><span>Copyright © 2017, Velmo. All rights reserved.</span><div class="socials"><span></span><span></span><span></span></div></div>
</footer>

<div class="veil"></div>

<div class="age-gate" role="dialog" aria-label="Age check">
  <h1>YOU MUST BE 21 OR OLDER TO ENTER</h1>
  <p>Nemo enim ipsam voluptatem quia voluptas sit aspernatur aut odit aut fugit, sed quia consequuntur magni dolores eos qui rati</p>
  <div class="gate-actions">
    <div class="gate-choice"><a class="gate-btn enter" href="#">Enter</a><small>I am Above 21</small></div>
    <div class="gate-choice"><a class="gate-btn exit" href="#">Exit</a><small>I am Under 21</small></div>
  </div>
</div>

</body>
</html>
```